Create a 2-sided postcard design (standard size) for Torvel Systems, a professional low-voltage and security integration company.
Side 1 – Front (Marketing Side)
Headline / Intro:
"Torvel Systems – Security, Connectivity, and Peace of Mind."
Brief Overview / Summary:
Torvel Systems provides complete security and technology integration solutions for commercial, industrial, and multifamily properties. From access control to fire systems, we specialize in delivering seamless, scalable, and reliable installations supported by professional service and ongoing care.
Services Breakdown:
Access Control – Cloud-based and enterprise access solutions to manage entry and permissions.
CCTV / Video Surveillance – Protect your property with high-definition cameras and remote monitoring.
Intrusion Alarm – Professional-grade systems to detect and deter unauthorized access.
Audio-Visual – From conference rooms to distributed audio and digital displays.
Fire Systems – Code-compliant alarm systems with 24/7 UL monitoring and life-safety support.
Structured Data Cabling – Low-voltage and fiber cabling for reliable network infrastructure.
Trusted By (Logos):
Mabo, Plurentix, Gorvlane, Basquin Investments, Tuln Hardware, Quillmoor Games, Corvane Holding Experts, TRUNKform
Technology partners:
Include logos of brands like Zelto, Pelican Rim Signals, RWJ , Binary Lookout, Solmira, GNT, Blazemar
Contact Info:
📧 sales@torvelsystems.example
📞 760-555-0143
🌐 torvelsystems.example
🖼️ Side 2 – Back (Branding Side)
Primary Focus:
Large, centered Torvel Systems logo.
Subtext / Tagline (Optional):
“Your Security and Technology Partner.”
List of Services (Under Logo):
Access Control | CCTV | Intrusion Alarm | Audio-Visual | Fire | Data
🎨 Design Preferences:
Clean, modern, and professional layout.
Corporate tones (e.g., black and white, bold accents).
Use clean typography and icons for service areas.
Logo should be prominent on the back and represent the brand with strength and clarity.
Open to designer layout and creative interpretation as long as it stays on brand.
Industry/Entity Type
Commercial Security
Colors
Designer to choose only greyscale colors for use in the design.
Look and feel

```html
<!DOCTYPE html>
<html lang="en">
<head>
<meta charset="utf-8">
<title>Torvel Systems Postcard</title>
<link href="https://fonts.googleapis.com/css2?family=Oswald:wght@600;700&family=Montserrat:wght@400;500;600;700&display=swap" rel="stylesheet">
<style>
:root{
  --stage:#a4a4a6;
  --ink:#0f1720;
  --navy:#121c28;
  --blue:#1d72b8;
  --purple:#6b5fc7;
  --light:#eceef1;
  --white:#ffffff;
  --footer:#141414;
  --text-dark:#2b2f36;
  --icon-blue:#6f8fd6;
}
*{margin:0;padding:0;box-sizing:border-box}
html,body{width:1200px;height:749px;overflow:hidden;background:var(--stage)}
body{position:relative;font-family:'Montserrat',sans-serif}
.card{position:absolute;top:181px;width:580px;height:386px;overflow:hidden;box-shadow:0 6px 18px rgba(0,0,0,.3)}
.card--front{left:12px;background:var(--navy)}
.card--back{left:608px;background:var(--light)}
.shape{position:absolute;inset:0;width:580px;height:386px}

.headline{position:absolute;left:25px;font-family:'Oswald',sans-serif;font-weight:700;color:var(--white);line-height:1}
.headline--title{top:26px;font-size:36px}
.headline--sub{top:67px;font-size:21px;font-weight:600;color:#d9dde3}
.intro{position:absolute;left:25px;top:108px;width:320px;font-size:8.9px;line-height:10.8px;color:var(--white)}

.service-list{position:absolute;left:18px;top:186px;width:282px;list-style:none}
.service-list li{position:relative;padding-left:8px;font-size:8.6px;line-height:10.6px;color:#e6e9ee;margin-bottom:4.6px}
.service-list li::before{content:"";position:absolute;left:-1px;top:2.5px;width:5px;height:5px;border:1px solid #cfd6df;border-radius:50%}
.service-list b{color:var(--white);font-weight:700}

.brand-mark{position:absolute;display:flex;align-items:center;gap:6px;color:var(--white);font-weight:600;letter-spacing:1px}
.brand-mark__square{border:2px solid var(--white)}
.brand-mark--front{right:22px;top:26px;font-size:15px}
.brand-mark--front .brand-mark__square{width:16px;height:16px}

.logo-box{position:absolute;left:355px;width:202px;background:var(--white);border:2px solid var(--purple)}
.logo-box--trusted{top:200px;height:59px}
.logo-box--partners{top:268px;height:65px}
.logo-box__tab{position:absolute;right:4px;top:-9px;background:var(--purple);color:var(--white);font-size:7.6px;font-weight:600;padding:1px 8px}
.logo-grid{position:absolute;inset:8px 5px 4px;display:grid;grid-template-columns:repeat(4,1fr);gap:2px 3px;align-items:center;justify-items:center;text-align:center}
.partner{font-size:6.2px;line-height:7px;font-weight:600;color:var(--text-dark)}
.partner--green{color:#3d9a6a}.partner--red{color:#c8262c}.partner--blue{color:#1f6fb5}.partner--orange{color:#e17a1c}.partner--violet{color:#8a3fa6}
.partner--large{font-size:9px;font-weight:700}

.footer{position:absolute;left:0;bottom:0;width:580px;height:40px;background:var(--footer);display:flex;align-items:center;justify-content:space-between;padding:0 18px;color:var(--white);font-size:11.6px}
.footer__item{display:flex;align-items:center;gap:6px}
.footer__item--phone{font-weight:700}
.footer svg{width:13px;height:13px}

.brand-mark--back{left:25px;top:30px;font-size:29px;font-weight:700;letter-spacing:2px}
.brand-mark--back .brand-mark__square{width:30px;height:30px;border-width:3px}
.tagline{position:absolute;left:25px;font-family:'Oswald',sans-serif;font-weight:700;font-size:30px;line-height:1}
.tagline--one{top:123px;color:var(--white)}
.tagline--two{top:161px;color:var(--ink)}
.services-heading{position:absolute;left:25px;top:213px;font-size:17px;font-weight:600;color:var(--white)}
.service-icons{position:absolute;left:24px;top:253px;display:grid;grid-template-columns:162px 130px;row-gap:4px;list-style:none}
.service-icons li{display:flex;align-items:center;gap:7px;font-size:14.5px;color:var(--ink);height:20px}
.service-icons svg{width:20px;height:20px}
.stamp-box{position:absolute;left:495px;top:24px;width:61px;height:61px;border:1px solid #666}
.address-line{position:absolute;left:349px;width:196px;height:1px;background:#8a8a8e}
</style>
</head>
<body>

<section class="card card--front" aria-label="Postcard front">
  <svg class="shape" viewBox="0 0 580 386" aria-hidden="true">
    <defs>
      <linearGradient id="introBand" x1="0" x2="1">
        <stop offset="0" stop-color="#1d72b8"/><stop offset=".7" stop-color="#17528a" stop-opacity=".85"/><stop offset="1" stop-color="#121c28" stop-opacity="0"/>
      </linearGradient>
      <linearGradient id="monitorRoom" x1="0" y1="0" x2="1" y2="1">
        <stop offset="0" stop-color="#0d2a4a"/><stop offset=".5" stop-color="#1f5c92"/><stop offset="1" stop-color="#0a1826"/>
      </linearGradient>
      <linearGradient id="panelLight" x1="0" x2="1">
        <stop offset="0" stop-color="#e4e6ea"/><stop offset="1" stop-color="#f4f5f7"/>
      </linearGradient>
    </defs>
    <rect x="0" y="104" width="420" height="72" fill="url(#introBand)"/>
    <polygon points="357,176 580,176 580,346 304,346" fill="url(#panelLight)"/>
    <polygon points="402,0 410,0 360,176 352,176" fill="#ffffff"/>
    <polygon points="410,0 580,0 580,176 360,176" fill="url(#monitorRoom)" role="img" aria-label="Photo of a security operator at a bank of monitoring screens"/>
  </svg>

  <h1 class="headline headline--title">Torvel Systems</h1>
  <p class="headline headline--sub">Security, Connectivity &amp; Peace of Mind</p>
  <p class="intro">Torvel Systems provides complete security and technology integration solutions for commercial, industrial, and multifamily properties. From access control to fire systems, we specialize in delivering seamless, scalable, and reliable installations supported by professional service and ongoing care.</p>

  <ul class="service-list">
    <li><b>Access Control –</b> Cloud-based and enterprise access solutions to manage entry and permissions.</li>
    <li><b>CCTV / Video Surveillance –</b> Protect your property with high-definition cameras and remote monitoring.</li>
    <li><b>Intrusion Alarm –</b> Professional-grade systems to detect and deter unauthorized access.</li>
    <li><b>Audio-Visual –</b> From conference rooms to distributed audio and digital displays.</li>
    <li><b>Fire Systems –</b> Code-compliant alarm systems with 24/7 UL monitoring and life-safety support.</li>
    <li><b>Structured Data Cabling –</b> Low-voltage and fiber cabling for reliable network infrastructure.</li>
  </ul>

  <div class="brand-mark brand-mark--front"><span class="brand-mark__square"></span>TORVEL SYSTEMS</div>

  <div class="logo-box logo-box--trusted">
    <span class="logo-box__tab">Trusted By</span>
    <div class="logo-grid">
      <span class="partner">Plurentix</span>
      <span class="partner partner--green">Gorvlane</span>
      <span class="partner">TRUNKform</span>
      <span class="partner partner--violet">Mabo</span>
      <span class="partner">Basquin Investments</span>
      <span class="partner partner--red">Tuln Hardware</span>
      <span class="partner partner--blue">Corvane Holding Experts</span>
      <span class="partner">Quillmoor Games</span>
    </div>
  </div>

  <div class="logo-box logo-box--partners">
    <span class="logo-box__tab">Technology Partners</span>
    <div class="logo-grid">
      <span class="partner partner--blue">Zelto</span>
      <span class="partner partner--orange partner--large">GNT</span>
      <span class="partner">Solmira</span>
      <span class="partner partner--blue partner--large">RWJ</span>
      <span class="partner">Blazemar Alarms</span>
      <span class="partner partner--blue">Pelican Rim Signals</span>
      <span class="partner">Binary Lookout</span>
    </div>
  </div>

  <footer class="footer">
    <span class="footer__item footer__item--phone"><svg viewBox="0 0 16 16" aria-hidden="true"><path d="M4 1.5l2.2 3-1.3 1.6a8 8 0 0 0 5 5l1.6-1.3 3 2.2-1.2 2.3C8.5 14.5 1.5 7.5 1.7 2.7z" fill="var(--icon-blue)"/></svg>760-555-0143</span>
    <span class="footer__item"><svg viewBox="0 0 16 16" aria-hidden="true"><rect x="1" y="3" width="14" height="10" fill="none" stroke="var(--icon-blue)" stroke-width="1.6"/><path d="M1 3l7 6 7-6" fill="none" stroke="var(--icon-blue)" stroke-width="1.6"/></svg>sales@torvelsystems.example</span>
    <span class="footer__item"><svg viewBox="0 0 16 16" aria-hidden="true"><circle cx="8" cy="8" r="6.5" fill="none" stroke="var(--icon-blue)" stroke-width="1.4"/><ellipse cx="8" cy="8" rx="2.8" ry="6.5" fill="none" stroke="var(--icon-blue)" stroke-width="1.2"/><path d="M1.5 8h13" stroke="var(--icon-blue)" stroke-width="1.2"/></svg>torvelsystems.example</span>
  </footer>
</section>

<section class="card card--back" aria-label="Postcard back">
  <svg class="shape" viewBox="0 0 580 386" aria-hidden="true">
    <defs>
      <linearGradient id="cameraPhoto" x1="0" y1="0" x2="1" y2="1">
        <stop offset="0" stop-color="#1a2330"/><stop offset=".6" stop-color="#55606e"/><stop offset="1" stop-color="#2a323c"/>
      </linearGradient>
      <linearGradient id="backPanel" x1="0" x2="1">
        <stop offset="0" stop-color="#dcdde1"/><stop offset="1" stop-color="#f2f3f5"/>
      </linearGradient>
      <linearGradient id="taglineBand" x1="0" x2="1">
        <stop offset="0" stop-color="#c9cacf"/><stop offset="1" stop-color="#9c9ea4"/>
      </linearGradient>
    </defs>
    <rect x="0" y="0" width="580" height="346" fill="url(#backPanel)"/>
    <polygon points="404,0 580,0 580,346 304,346" fill="#ffffff"/>
    <polygon points="0,0 324,0 262,157 0,157" fill="#0f151c"/>
    <polygon points="150,0 324,0 262,157 180,157" fill="url(#cameraPhoto)" role="img" aria-label="Photo of a mounted security dome camera"/>
    <polygon points="0,117 276,117 262,157 0,157" fill="#1b2129"/>
    <polygon points="0,157 262,157 246,197 0,197" fill="url(#taglineBand)"/>
    <polygon points="0,211 186,211 178,236 0,236" fill="var(--purple)"/>
  </svg>

  <div class="brand-mark brand-mark--back"><span class="brand-mark__square"></span>TORVEL SYSTEMS</div>
  <p class="tagline tagline--one">Your Security &amp;</p>
  <p class="tagline tagline--two">Technology Partner</p>
  <h2 class="services-heading">Our Services</h2>

  <ul class="service-icons">
    <li><svg viewBox="0 0 20 20" aria-hidden="true"><rect width="20" height="20" fill="#1b1f25"/><rect x="5" y="4" width="6" height="12" fill="none" stroke="#fff" stroke-width="1.3"/><circle cx="14" cy="8" r="1.5" fill="#fff"/><rect x="13.3" y="10" width="1.4" height="5" fill="#fff"/></svg>Access Control</li>
    <li><svg viewBox="0 0 20 20" aria-hidden="true"><rect width="20" height="20" fill="#1b1f25"/><rect x="6" y="3" width="8" height="14" rx="1" fill="none" stroke="#fff" stroke-width="1.3"/><path d="M8 8h4M8 11h4" stroke="#fff" stroke-width="1.2"/></svg>Audio-Visual</li>
    <li><svg viewBox="0 0 20 20" aria-hidden="true"><rect width="20" height="20" fill="#1b1f25"/><rect x="3" y="6" width="11" height="5" fill="#fff"/><path d="M14 8l3-1.5v5L14 10" fill="#fff"/><path d="M6 11v4h-2" stroke="#fff" stroke-width="1.4" fill="none"/></svg>CCTV</li>
    <li><svg viewBox="0 0 20 20" aria-hidden="true"><rect width="20" height="20" fill="#1b1f25"/><path d="M10 3c1 3 5 5 5 9a5 5 0 0 1-10 0c0-2 1-3 2-4 0 2 1 3 2 3 0-3 0-5 1-8z" fill="#fff"/></svg>Fire</li>
    <li><svg viewBox="0 0 20 20" aria-hidden="true"><rect width="20" height="20" fill="#1b1f25"/><path d="M5 14a5 5 0 0 1 10 0z" fill="#fff"/><rect x="3" y="14" width="14" height="2" fill="#fff"/><path d="M10 3v3M4 6l2 2M16 6l-2 2" stroke="#fff" stroke-width="1.3"/></svg>Intrusion Alarm</li>
    <li><svg viewBox="0 0 20 20" aria-hidden="true"><rect width="20" height="20" fill="#1b1f25"/><rect x="3" y="4" width="14" height="12" fill="none" stroke="#fff" stroke-width="1.3"/><rect x="6" y="10" width="2" height="4" fill="#fff"/><rect x="9" y="8" width="2" height="6" fill="#fff"/><rect x="12" y="6" width="2" height="8" fill="#fff"/></svg>Data</li>
  </ul>

  <div class="stamp-box"></div>
  <span class="address-line" style="top:212px"></span>
  <span class="address-line" style="top:234px"></span>
  <span class="address-line" style="top:257px"></span>
  <span class="address-line" style="top:279px"></span>
  <span class="address-line" style="top:302px"></span>

  <footer class="footer">
    <span class="footer__item footer__item--phone"><svg viewBox="0 0 16 16" aria-hidden="true"><path d="M4 1.5l2.2 3-1.3 1.6a8 8 0 0 0 5 5l1.6-1.3 3 2.2-1.2 2.3C8.5 14.5 1.5 7.5 1.7 2.7z" fill="var(--icon-blue)"/></svg>760-555-0143</span>
    <span class="footer__item"><svg viewBox="0 0 16 16" aria-hidden="true"><rect x="1" y="3" width="14" height="10" fill="none" stroke="var(--icon-blue)" stroke-width="1.6"/><path d="M1 3l7 6 7-6" fill="none" stroke="var(--icon-blue)" stroke-width="1.6"/></svg>sales@torvelsystems.example</span>
    <span class="footer__item"><svg viewBox="0 0 16 16" aria-hidden="true"><circle cx="8" cy="8" r="6.5" fill="none" stroke="var(--icon-blue)" stroke-width="1.4"/><ellipse cx="8" cy="8" rx="2.8" ry="6.5" fill="none" stroke="var(--icon-blue)" stroke-width="1.2"/><path d="M1.5 8h13" stroke="var(--icon-blue)" stroke-width="1.2"/></svg>torvelsystems.example</span>
  </footer>
</section>

</body>
</html>
```